Lotus Market Hall VIP Card(Magnetic strip plastic card)

We need Fancy,Simple,VIP customer card design for a grocery store name"Lotus Market Hall", Chinese name"福润商场“.Major color should be Dark red. This design is based on a VIP gift card project, which means design should consider about the back side with magnetic strip area and mostly it will be plastic material.

Target Market(s)

Rich Customers

Industry/Entity Type

Grocery Store

Contact Information for Business Card

People actually put more than $1000 into the card for shopping

Font styles to use
Serif
Sans Serif
Decorative
Script
Other font styles liked:
• Fancy

Colors
ec1f27
fbed22

Requirements
Must have
• Red color
Nice to have
• Better logo transformation.

```html
<!DOCTYPE html>
<html lang="en">
<head>
<meta charset="utf-8">
<title>Lotus Market Hall VIP Card</title>
<link rel="stylesheet" href="https://fonts.googleapis.com/css2?family=Arimo:wght@400;700&family=Noto+Sans+SC:wght@700&display=swap">
<style>
  :root {
    --page: #ffffff;
    --card-black: #000000;
    --card-white: #ffffff;
    --brand-red: #ec1f27;
    --brand-yellow: #fbed22;
    --dragon-deep: #6b6200;
    --ghost-grey: #e4e4e4;
    --stripe: #000000;
    --ink: #111111;
    --fine-print: #6a6a6a;
    --edge: #e3e3e3;
  }
  * { margin: 0; padding: 0; box-sizing: border-box; }
  html, body {
    width: 1200px; height: 816px; overflow: hidden;
    background: var(--page);
    font-family: "Arimo", Arial, sans-serif;
  }
  .canvas { position: relative; width: 1200px; height: 816px; }

  .card { position: absolute; border-radius: 16px; overflow: hidden; }

  /* Back of card */
  .card-back {
    left: 513px; top: 345px; width: 584px; height: 364px;
    background: var(--card-white);
    border: 1px solid var(--edge);
  }
  .back-artwork {
    position: absolute; inset: 0;
    background: radial-gradient(ellipse 70% 60% at 55% 45%, var(--ghost-grey), rgba(255,255,255,0) 75%);
  }
  .magnetic-stripe {
    position: absolute; left: 0; right: 0; top: 83px; height: 42px;
    background: var(--stripe);
  }
  .holder-name {
    position: absolute; left: 180px; top: 166px;
    font-size: 27px; letter-spacing: 1.5px; color: var(--ink);
  }
  .fine-print {
    position: absolute; left: 20px; right: 16px; top: 247px;
    font-size: 8.4px; line-height: 12px; color: var(--fine-print);
  }
  .fine-print p + p { margin-top: 0; }
  .fine-print .gap { margin-top: 12px; }

  /* Front of card */
  .card-front {
    left: 94px; top: 114px; width: 586px; height: 366px;
    background: var(--card-black);
  }
  .front-artwork {
    position: absolute; inset: 0;
    background:
      radial-gradient(ellipse 42% 55% at 24% 40%, rgba(251,237,34,0.75), rgba(251,237,34,0) 70%),
      radial-gradient(ellipse 45% 60% at 78% 45%, rgba(251,237,34,0.8), rgba(251,237,34,0) 72%),
      radial-gradient(ellipse 60% 30% at 55% 8%, rgba(251,237,34,0.7), rgba(251,237,34,0) 75%);
  }
  .brand {
    position: absolute; left: 0; right: 0; top: 118px;
    text-align: center; color: var(--brand-red); font-weight: 700;
  }
  .brand-chinese {
    font-family: "Noto Sans SC", "Arimo", sans-serif;
    font-size: 62px; line-height: 76px; letter-spacing: 4px;
  }
  .brand-name {
    font-family: "Arimo", Arial, sans-serif;
    font-size: 30px; line-height: 34px;
  }
  .vip-label {
    position: absolute; left: 0; right: 0; top: 262px;
    text-align: center; font-weight: 700; font-size: 26px;
    letter-spacing: 7px; color: var(--brand-yellow);
  }
</style>
</head>
<body>
<main class="canvas">
  <section class="card card-back" aria-label="Card back">
    <div class="back-artwork" role="img" aria-label="Faint grey dragon illustration across the card back"></div>
    <div class="magnetic-stripe"></div>
    <div class="holder-name">JORDAN WELLS</div>
    <div class="fine-print">
      <p>CASHIER NOTICE: Photo ID is required to use this VIP Card, photo ID must match the name printed on the back of Card. This is not a credit/debit card and has no implied warranties or purchase protection. Please present this card to the cashier at the time of purchase. This Card may not be redeemed for cash except in States where required. Merchant is not responsible for lost, stolen, or damaged Cards or any unauthorized use.</p>
      <p>LOST/FIND: If you lose or find this Card please call LMH at 206-555-0148 immediately. Thank you.</p>
      <p class="gap">To check your Card Balance anytime call 1-888-555-0163 and input your Card number.</p>
    </div>
  </section>

  <section class="card card-front" aria-label="Card front">
    <div class="front-artwork" role="img" aria-label="Large yellow dragon illustration coiling across the black card front"></div>
    <div class="brand">
      <div class="brand-chinese">福润商场</div>
      <div class="brand-name">Lotus Market Hall</div>
    </div>
    <div class="vip-label">VIP</div>
  </section>
</main>
</body>
</html>
```